Business card design needed

I run a Beautician studio (for 7 years now)
I offer
- Velmo Body Sugaring
- Ruby Glaze
- Nails
- Facials
- Manicure
- Foot Treatment
It might not be necessary to list all those treatments?
Maybe the link to the Website is sufficient?
I leave that up to you ...
(more info on www.FernAndDewByLenka.com.au)
Velmo BodySugaring is our biggest success, It replaces waxing.
I would like to incorporate the logo into the Business Card.
We had many complaints regarding our old Business Cards as the Phone Number was to small.
On the backside, we would like a "your next Appointment" section.
Looking forward to you Design, cheers ... Lenka
Industry/Entity Type
Business
Contact Information for Business Card
Fern by Dew by Lenka
14 Korrin Sqr 3942 Berwick
www.FernAndDewByLenka.com.au
03 9481 2267

```html
<!DOCTYPE html>
<html lang="en">
<head>
<meta charset="utf-8">
<title>Fern by Dew by Lenka – Business &amp; Appointment Cards</title>
<link rel="stylesheet" href="https://fonts.googleapis.com/css2?family=Arimo:wght@400;700&family=Open+Sans:wght@400;600;700&family=Cinzel:wght@500&display=swap">
<style>
:root{
  --backdrop:#1c1c1c;
  --card:#ffffff;
  --ink:#3a3a3a;
  --ink-soft:#555555;
  --green:#1a9a45;
  --sun:#f0a020;
  --rule:#9a9a9a;
  --box:#7a7a7a;
}
*{margin:0;padding:0;box-sizing:border-box}
html,body{width:1200px;height:720px;overflow:hidden;background:var(--backdrop)}
.stage{position:relative;width:1200px;height:720px}
.card{position:absolute;width:524px;height:299px;background:var(--card);font-family:"Open Sans",Arial,sans-serif;color:var(--ink)}
.card > *{position:absolute;white-space:nowrap}
.front{left:310px;top:31px;font-family:Arimo,Arial,sans-serif}
.appointment{left:57px;top:366px}
.reminder{left:611px;top:368px}

/* front */
.business-name{left:30px;top:33px;font-size:24px;font-weight:700;color:var(--ink)}
.address{left:30px;top:63px;font-size:14px}
.contact{left:30px;display:flex;align-items:center;gap:8px}
.contact svg{flex:none}
.phone{top:99px;font-size:17px}
.web{top:128px;font-size:14px}
.treatments-title{left:30px;top:164px;font-size:17px;font-weight:700;color:var(--green);letter-spacing:1px}
.treatments{left:30px;top:187px;list-style:none;font-size:14px;line-height:21px}

/* brand mark stand-in */
.brand{display:flex;flex-direction:column;align-items:center;gap:8px;text-align:center}
.brand-dot{width:46px;height:46px;border-radius:50%;background:var(--sun)}
.brand-name{font-family:"Open Sans",Arial,sans-serif;font-weight:600;color:var(--ink);font-size:13px;letter-spacing:1px;text-transform:uppercase;line-height:1.3;white-space:normal}
.front .brand{left:335px;top:160px;width:170px}
.appointment .brand{left:325px;top:22px;width:140px}
.reminder .brand{left:30px;top:150px;width:125px}

/* shared */
.hours-title{font-size:21px;color:var(--green);letter-spacing:1px}
.hours{font-size:14.5px;font-weight:700;line-height:22px;color:var(--ink-soft)}
.appointment .hours-title{left:31px;top:9px}
.appointment .hours{left:31px;top:38px}
.section-title{left:35px;top:95px;font-family:Cinzel,Georgia,serif;font-size:18px;color:var(--green)}
.field{left:35px;font-size:15px;display:flex;align-items:flex-end;gap:6px;color:var(--ink-soft)}
.blank{display:inline-block;border-bottom:1px solid var(--rule);height:1px;margin-bottom:4px}
.blank.dotted{border-bottom-style:dotted}
.box{display:inline-block;border:1px solid var(--box);border-radius:2px}
.name-field{top:132px}
.date-field{top:170px}
.next-field{top:206px;align-items:center;gap:0}
.next-field .box{width:95px;height:21px;margin-left:12px}
.next-field .box + .box{margin-left:32px}
.days{display:flex;align-items:center;font-size:15px;color:var(--ink-soft)}
.appointment .days{left:31px;top:244px}
.appointment .days .box{width:33px;height:20px;margin:0 7px 0 6px}
.notice{left:0;width:524px;top:277px;text-align:center;font-size:11px;color:var(--ink)}

/* reminder */
.reminder .hours-title{left:34px;top:57px}
.reminder .hours{left:34px;top:86px}
.divider{left:257px;top:37px;width:1px;height:225px;background:linear-gradient(var(--card),#b5b5b5 15%,#b5b5b5 85%,var(--card))}
.holder-line{left:276px;top:42px;width:218px;border-bottom:1px dotted var(--rule)}
.holder-label{left:276px;top:51px;font-size:15px;font-weight:600;color:var(--ink-soft)}
.day-grid{left:276px;top:94px;display:flex;gap:10px}
.day{display:flex;flex-direction:column;align-items:center;gap:4px;font-size:14px;color:var(--ink-soft)}
.day .box{width:16px;height:11px}
.reminder .field{left:276px;color:var(--ink)}
.reminder .date-line{top:142px}
.reminder .time-line{top:172px}
.cancel-note{left:276px;top:213px;font-size:15px;line-height:21px;white-space:normal;width:230px;color:var(--ink-soft)}
</style>
</head>
<body>
<main class="stage">

  <section class="card front" aria-label="Business card front">
    <h1 class="business-name">Fern by Dew by Lenka</h1>
    <p class="address">14 Korrin Sqr 3942 Berwick</p>
    <p class="contact phone">
      <svg width="15" height="16" viewBox="0 0 15 16" aria-hidden="true"><circle cx="7.5" cy="8" r="6.6" fill="none" stroke="#1a9a45" stroke-width="1.4"/><path d="M5 4.5c.6-.4 1.1 0 1.3.6l.3 1.1c.1.4-.2.7-.5.9.3 1.2 1 2 2 2.5.3-.3.6-.6 1-.4l1 .5c.5.3.7.8.3 1.3-.7.8-1.7.9-2.8.3C6 10.4 4.8 8.8 4.5 7 4.3 5.9 4.4 5 5 4.5z" fill="#1a9a45"/></svg>
      03 9481 2267
    </p>
    <p class="contact web">
      <svg width="13" height="13" viewBox="0 0 14 14" aria-hidden="true"><g fill="none" stroke="#1a9a45" stroke-width="1.2"><circle cx="7" cy="7" r="6"/><ellipse cx="7" cy="7" rx="2.6" ry="6"/><path d="M1 7h12M2 3.8h10M2 10.2h10"/></g></svg>
      www.FernAndDewByLenka.com.au
    </p>
    <h2 class="treatments-title">Treatments offer</h2>
    <ul class="treatments">
      <li>• Velmo Body Sugaring</li>
      <li>• Ruby Glaze • Nails</li>
      <li>• Facials • Manicure</li>
      <li>• Foot Treatment</li>
    </ul>
    <div class="brand"><span class="brand-dot"></span><span class="brand-name">Velmo Body Sugaring</span></div>
  </section>

  <section class="card appointment" aria-label="Appointment card">
    <h2 class="hours-title">Hours of Operation</h2>
    <p class="hours">Mon - Fri:&nbsp; 7.30am - 7.00pm<br>Saturday: 7.30am - 12.00pm</p>
    <div class="brand"><span class="brand-dot"></span><span class="brand-name">Velmo Body Sugaring</span></div>
    <h3 class="section-title">YOUR APPOINTMENT</h3>
    <p class="field name-field">Name :&nbsp;&nbsp; <span class="blank dotted" style="width:290px"></span></p>
    <p class="field date-field">Date :&nbsp;&nbsp;&nbsp;&nbsp; <span class="blank" style="width:95px"></span>&nbsp;Time : <span class="blank" style="width:88px"></span> am / pm</p>
    <p class="field next-field">Next Appointment <span class="box"></span><span class="box"></span></p>
    <p class="days">MON<span class="box"></span>TUE<span class="box"></span>WED<span class="box"></span>THU<span class="box"></span>FRI<span class="box"></span>SAT<span class="box"></span></p>
    <p class="notice">It would be appreciated if 24 hours notice could be given if you are unable to attend an appointment</p>
  </section>

  <section class="card reminder" aria-label="Appointment reminder card">
    <h2 class="hours-title">Hours of Operation</h2>
    <p class="hours">Mon - Fri:&nbsp; 7.30am - 7.00pm<br>Saturday: 7.30am - 12.00pm</p>
    <div class="brand"><span class="brand-dot"></span><span class="brand-name">Velmo Body Sugaring</span></div>
    <span class="divider"></span>
    <span class="holder-line"></span>
    <p class="holder-label">has an appointment</p>
    <div class="day-grid">
      <span class="day">MON<span class="box"></span></span>
      <span class="day">TUE<span class="box"></span></span>
      <span class="day">WED<span class="box"></span></span>
      <span class="day">THU<span class="box"></span></span>
      <span class="day">FRI<span class="box"></span></span>
      <span class="day">SAT<span class="box"></span></span>
    </div>
    <p class="field date-line">Date : <span class="blank" style="width:148px"></span></p>
    <p class="field time-line">Time : <span class="blank" style="width:122px"></span> AM/PM</p>
    <p class="cancel-note">Advance notice requested for appointment cancellation</p>
  </section>

</main>
</body>
</html>
```